Bildevold buisnesscard

Hey :) I need a modern buisnesscard for my company Bildevold
It most have:
Dagligleder og Fotograf: Henrik Audun Strandvik

Mob: +4791264085
Epost: post@bildevold.example
Adresse: Kvernbakken9, 6040 Fjordvik

Facbook and instagram logo with text Bildevold

Bildevold logo

It Company

```html
<!DOCTYPE html>
<html lang="no">
<head>
<meta charset="utf-8">
<title>Bildevold – visittkort</title>
<link rel="stylesheet" href="https://fonts.googleapis.com/css2?family=Exo+2:wght@600;700&family=Open+Sans:wght@400&display=swap">
<style>
  :root {
    --page-bg: #d9d9d9;
    --brand-blue: #2d8bc0;
    --brand-pink: #c63d86;
    --card-white: #f4f4f4;
    --card-dark: #2b2b2c;
    --ink: #3a3a3a;
    --dots: #555;
    --social-blue: #2f4d9a;
    --social-gold: #d6a93c;
  }
  * { margin: 0; padding: 0; box-sizing: border-box; }
  html, body { width: 1200px; height: 799px; overflow: hidden; }
  body {
    background: var(--page-bg);
    position: relative;
    font-family: "Open Sans", Arial, sans-serif;
  }
  .card {
    position: absolute;
    top: 110px;
    width: 330px;
    height: 578px;
    overflow: hidden;
    box-shadow: 0 8px 24px rgba(0,0,0,.25);
  }
  .card-front { left: 225px; background: var(--card-white); }
  .card-back { left: 645px; background: var(--card-dark); }

  .header-band { position: absolute; top: 0; left: 0; width: 330px; height: 230px; }
  .header-text {
    position: absolute; top: 42px; left: 0; width: 100%;
    text-align: center; color: #fff;
    font-family: "Exo 2", Arial, sans-serif;
  }
  .person-name { font-size: 21px; font-weight: 700; letter-spacing: .3px; }
  .person-role { font-size: 15px; font-weight: 600; margin-top: 4px; }
  .person-phone { font-size: 24px; font-weight: 700; margin-top: 2px; letter-spacing: .5px; }

  .brand-name {
    font-family: "Exo 2", Arial, sans-serif;
    font-weight: 700;
    letter-spacing: .5px;
  }
  .card-front .brand-name {
    position: absolute; top: 278px; left: 0; width: 100%;
    text-align: center; font-size: 40px; color: var(--brand-blue);
  }
  .contact-block {
    position: absolute; top: 352px; left: 38px; width: 254px;
    border-top: 2px dotted var(--dots);
    border-bottom: 2px dotted var(--dots);
    padding: 12px 0 14px;
    text-align: center; color: var(--ink);
    font-size: 14px; line-height: 1.35;
  }
  .social-row {
    position: absolute; top: 468px; left: 0; width: 100%;
    display: flex; justify-content: center; gap: 10px;
  }
  .social-dot { width: 26px; height: 26px; border-radius: 50%; }
  .social-dot.fb { background: var(--social-blue); }
  .social-dot.ig { background: var(--social-gold); }

  .footer-band {
    position: absolute; bottom: 0; left: 0; width: 100%; height: 22px;
    background: var(--brand-pink);
  }
  .card-back .brand-name {
    position: absolute; top: 250px; left: 0; width: 100%;
    text-align: center; font-size: 44px; color: var(--brand-pink);
  }
</style>
</head>
<body>
  <section class="card card-front">
    <svg class="header-band" viewBox="0 0 330 230" aria-hidden="true">
      <polygon points="0,0 330,0 330,170 195,170 165,230 135,170 0,170" fill="var(--brand-blue)"/>
    </svg>
    <div class="header-text">
      <p class="person-name">Henrik Audun Strandvik</p>
      <p class="person-role">Dagligleder og Fotograf</p>
      <p class="person-phone">+4791264085</p>
    </div>
    <p class="brand-name">Bildevold</p>
    <div class="contact-block">
      <p>post@bildevold.example</p>
      <p>Kvernbakken9, 6040 Fjordvik</p>
      <p>www.bildevold.example</p>
    </div>
    <div class="social-row">
      <span class="social-dot fb"></span>
      <span class="social-dot ig"></span>
    </div>
    <div class="footer-band"></div>
  </section>

  <section class="card card-back">
    <p class="brand-name">Bildevold</p>
    <div class="footer-band"></div>
  </section>
</body>
</html>
```